creation of a business card design for a company specializing in the creation...

I would like to create a design for a professional business card on a black background and with the company's colors (I am attaching some files: including the logo in horizontal and centered format, I am also attaching a recent project design a T-shirt, this is the one I chose to give you an idea of my preferences.

we are in the process of developing a new website design, it is still in the development phase but it can be viewed at the following address: www.vantrelmo.be to give you other ideas about the company
you will see for yourself the subject of my main activity: company specializing in the construction of stairs

I would like a business card that stands out from the rest with a unique design

here is the informations
Name: Lucien Barthel
Function: Manager
Address: Rue Moulinet du Parc 42
7180 Marbrelle
telephone: +32 468 219 804
email: info@rx7p.be
website: rx7p. be
social networks: Facebook, YouTube, TikTok, Instagram

Target Market(s)

customer who wants to have a beautiful staircase built

Industry/Entity Type

contruction d'escalier

Contact Information for Business Card

Adresse. Numero de telephone, site web, le texte : "Createur d'escalier", logo recto-verso, icone des reseaux sociaux

Requirements
Must have
• the mention: Stair creator
Nice to have
• an illustration of a designer staircase
Should not have
• do not distort the logo

```html
<!DOCTYPE html>
<html lang="en">
<head>
<meta charset="utf-8">
<title>RX7P Business Card</title>
<link href="https://fonts.googleapis.com/css2?family=Montserrat:wght@400;500;700&display=swap" rel="stylesheet">
<style>
  :root {
    --backdrop: #2e2e2f;
    --card: #161617;
    --card-edge: #6a9cc4;
    --accent: #6f9fca;
    --text: #f2f2f2;
    --muted: #9fb3c4;
    --rule: #4f7fa6;
  }
  html, body {
    margin: 0;
    width: 1200px;
    height: 801px;
    overflow: hidden;
    background: var(--backdrop);
    font-family: "Montserrat", sans-serif;
  }
  .stage {
    position: relative;
    width: 1200px;
    height: 801px;
  }
  .card {
    position: absolute;
    top: 250px;
    width: 540px;
    height: 300px;
    background: var(--card);
    border: 2px solid var(--card-edge);
    box-sizing: border-box;
    overflow: hidden;
    color: var(--text);
  }
  .card--front { left: 40px; }
  .card--back { left: 620px; }

  /* brand lockup */
  .brand {
    position: absolute;
    display: flex;
    align-items: center;
    gap: 10px;
  }
  .brand__mark {
    width: 30px;
    height: 30px;
    background: var(--accent);
    flex: none;
  }
  .brand__text {
    display: flex;
    flex-direction: column;
    align-items: flex-start;
  }
  .brand__name {
    font-weight: 500;
    font-size: 36px;
    letter-spacing: 5px;
    color: var(--text);
    line-height: 1;
  }
  .brand__tagline {
    margin-top: 6px;
    font-size: 8px;
    letter-spacing: 4px;
    color: var(--muted);
    text-transform: uppercase;
    white-space: nowrap;
  }
  .card--front .brand { left: 30px; top: 62px; }
  .card--back .brand { right: 36px; top: 196px; }

  /* front details */
  .person {
    position: absolute;
    right: 28px;
    top: 106px;
    text-align: right;
  }
  .person__name {
    font-weight: 700;
    font-size: 20px;
    color: var(--accent);
    text-transform: uppercase;
    letter-spacing: 0.3px;
    line-height: 1.1;
  }
  .person__role {
    font-size: 13px;
    margin-top: 3px;
  }
  .rule {
    position: absolute;
    left: 32px;
    right: 0;
    top: 180px;
    height: 1px;
    background: var(--rule);
  }
  .address {
    position: absolute;
    right: 28px;
    top: 192px;
    text-align: right;
    font-size: 13px;
    line-height: 1.45;
  }
  .socials {
    display: flex;
    justify-content: flex-end;
    gap: 5px;
    margin-top: 5px;
  }
  .socials__dot {
    width: 12px;
    height: 12px;
    border-radius: 50%;
    background: var(--accent);
  }
  .contact {
    position: absolute;
    left: 32px;
    top: 196px;
    margin: 0;
    padding: 0;
    list-style: none;
    font-size: 13px;
    line-height: 1.6;
  }
  .contact li {
    display: flex;
    align-items: center;
    gap: 9px;
  }
  .contact svg { width: 11px; height: 11px; flex: none; }

  /* back */
  .pattern {
    position: absolute;
    inset: 0;
    background: linear-gradient(120deg, #0b0b0c 0%, #1a1a1b 45%, #2a2a2b 100%);
  }
</style>
</head>
<body>
<main class="stage">

  <section class="card card--front" aria-label="Business card front">
    <div class="brand">
      <span class="brand__mark"></span>
      <div class="brand__text">
        <span class="brand__name">RX7P</span>
        <span class="brand__tagline">Bespoke Stairways</span>
      </div>
    </div>

    <div class="person">
      <div class="person__name">Lucien Barthel</div>
      <div class="person__role">Manager</div>
    </div>

    <div class="rule"></div>

    <ul class="contact">
      <li>
        <svg viewBox="0 0 12 12" aria-hidden="true"><path d="M2.5 1h2l1 3-1.3 1a6 6 0 0 0 2.8 2.8l1-1.3 3 1v2a1 1 0 0 1-1 1A9.5 9.5 0 0 1 1.5 2a1 1 0 0 1 1-1z" fill="var(--accent)"/></svg>
        +32 468 219 804
      </li>
      <li>
        <svg viewBox="0 0 12 12" aria-hidden="true"><rect x="0.5" y="2.5" width="11" height="7" fill="var(--accent)"/><path d="M0.5 2.5 6 6.5l5.5-4" stroke="var(--card)" fill="none"/></svg>
        info@rx7p.be
      </li>
      <li>
        <svg viewBox="0 0 12 12" aria-hidden="true"><circle cx="6" cy="6" r="5.5" fill="var(--accent)"/><path d="M0.5 6h11M6 0.5c-3 3-3 8 0 11M6 0.5c3 3 3 8 0 11" stroke="var(--card)" fill="none" stroke-width="0.8"/></svg>
        rx7p. be
      </li>
    </ul>

    <div class="address">
      Rue Moulinet du Parc 42<br>
      7180 Marbrelle
      <div class="socials" aria-label="Social networks">
        <span class="socials__dot"></span>
        <span class="socials__dot"></span>
        <span class="socials__dot"></span>
        <span class="socials__dot"></span>
      </div>
    </div>
  </section>

  <section class="card card--back" aria-label="Business card back">
    <div class="pattern" role="img" aria-label="Repeating tonal brand pattern in dark greys"></div>
    <div class="brand">
      <span class="brand__mark"></span>
      <div class="brand__text">
        <span class="brand__name">RX7P</span>
        <span class="brand__tagline">Bespoke Stairways</span>
      </div>
    </div>
  </section>

</main>
</body>
</html>
```